New Business Card Design Project

Use the flyer uploaded and website www.brightoakbuilders.com for inspiration.
List Our Services on Backside of business cards
Marcus Delling
Harborline Builders Inc.
Licensed General Contractors
858-471-6093

Contact Information for Business Card

Use the flyer uploaded and website www.brightoakbuilders.com for inspiration. List Our Services on Backside of business cards Marcus Delling Harborline Builders Inc. Licensed General Contractors 858-471-6093

```html
<!DOCTYPE html>
<html lang="en">
<head>
<meta charset="utf-8">
<title>Harborline Builders – Business Cards</title>
<link rel="stylesheet" href="https://fonts.googleapis.com/css2?family=Cinzel:wght@400;600&family=Montserrat:wght@400;500&display=swap">
<style>
  :root {
    --backdrop: #2b2b2b;
    --card: #151517;
    --accent: #e3141e;
    --ink: #ffffff;
    --ink-soft: #e8e8e8;
  }
  * { box-sizing: border-box; margin: 0; padding: 0; }
  html, body { width: 1200px; height: 900px; overflow: hidden; }
  body {
    background: var(--backdrop);
    display: flex;
    flex-direction: column;
    align-items: center;
    justify-content: center;
    gap: 44px;
    font-family: "Montserrat", sans-serif;
    color: var(--ink);
  }
  .card {
    position: relative;
    width: 660px;
    height: 377px;
    background: var(--card);
    border-bottom: 5px solid var(--accent);
    box-shadow: 0 14px 30px rgba(0,0,0,.45);
  }
  .brand {
    display: flex;
    align-items: center;
    gap: 12px;
  }
  .brand-dot {
    width: 12px; height: 12px; border-radius: 50%;
    background: var(--ink);
  }
  .brand-name {
    font-family: "Cinzel", serif;
    font-weight: 400;
    font-size: 30px;
    letter-spacing: 1px;
    color: var(--ink);
    text-transform: uppercase;
  }

  /* front side */
  .card-front {
    display: flex;
    flex-direction: column;
    align-items: center;
    justify-content: center;
    gap: 64px;
  }
  .services {
    text-align: center;
    font-size: 16px;
    line-height: 1.55;
    color: var(--ink-soft);
  }
  .services .sep { color: var(--accent); padding: 0 6px; }

  /* back side */
  .card-back .brand { position: absolute; left: 40px; top: 96px; }
  .card-back .brand-name { font-size: 26px; }
  .person { position: absolute; left: 48px; bottom: 46px; }
  .person-name {
    font-family: "Cinzel", serif;
    font-weight: 600;
    font-size: 26px;
    color: var(--accent);
    text-transform: uppercase;
    line-height: 1.1;
  }
  .person-title { font-size: 17px; color: var(--ink); margin-top: 2px; }
  .contact {
    position: absolute;
    right: 34px;
    top: 128px;
    list-style: none;
    font-size: 15px;
    line-height: 1.8;
  }
  .contact .company { margin-bottom: 10px; font-size: 16px; }
  .contact li { display: flex; align-items: center; gap: 10px; }
  .contact svg { width: 14px; height: 14px; fill: var(--accent); flex: none; }
</style>
</head>
<body>

<section class="card card-front" aria-label="Card front">
  <div class="brand">
    <span class="brand-dot"></span>
    <span class="brand-name">Harborline Builders</span>
  </div>
  <p class="services">
    Painting<span class="sep">•</span>Flooring<span class="sep">•</span>Kitchens<span class="sep">•</span>Custom Renovations<br>
    Bathrooms<span class="sep">•</span>Energy Efficienct Upgrades
  </p>
</section>

<section class="card card-back" aria-label="Card back">
  <div class="brand">
    <span class="brand-dot"></span>
    <span class="brand-name">Harborline Builders</span>
  </div>

  <div class="person">
    <p class="person-name">Marcus Delling</p>
    <p class="person-title">Licensed General Contractors</p>
  </div>

  <ul class="contact">
    <li class="company">Harborline Builders Inc.</li>
    <li>
      <svg viewBox="0 0 24 24" aria-hidden="true"><path d="M6.6 10.8a15.1 15.1 0 0 0 6.6 6.6l2.2-2.2a1 1 0 0 1 1-.25 11.4 11.4 0 0 0 3.6.57 1 1 0 0 1 1 1V20a1 1 0 0 1-1 1A17 17 0 0 1 3 4a1 1 0 0 1 1-1h3.5a1 1 0 0 1 1 1c0 1.25.2 2.45.57 3.57a1 1 0 0 1-.25 1z"/></svg>
      858-471-6093
    </li>
    <li>
      <svg viewBox="0 0 24 24" aria-hidden="true"><path d="M2 5h20v14H2z M2 5l10 8 10-8" fill="none" stroke="#e3141e" stroke-width="2.4"/></svg>
      info@brightoakbuilders.com
    </li>
    <li>
      <svg viewBox="0 0 24 24" aria-hidden="true"><circle cx="12" cy="12" r="9" fill="none" stroke="#e3141e" stroke-width="2.4"/><path d="M3 12h18M12 3c3 3 3 15 0 18M12 3c-3 3-3 15 0 18" fill="none" stroke="#e3141e" stroke-width="1.8"/></svg>
      www.brightoakbuilders.com
    </li>
  </ul>
</section>

</body>
</html>
```